New business card, letter head, email signature and Portfolio for our Security company.

We are an Crest security company that provides a top quality manpower services to protect high rise buildings, retail and all type of properties and would like a new business card/logo look.

- We would like the spot UV design.
- Matt black (double sided).
- We would like to incorporate a royal blue colour (feel free to experiment with it).
- Feel free to try different lengths with the card to make it stand out more than a normal business card.
- We would like the logo to be an eagle eye in the background (shines when card is tilted slightly in the background, either on the front, back or both sides of the card). Image attached as an example of eye shape (colour to be either black or royal blue).
- HARBOUR CREST SECURITY SERVICES PTY. LTD. and HCSS to be placed on one side of the card and on the other side of the card to have;

- Name in slightly bigger font than the position (directly on the bottom on the name).
- Mobile number
- Email address
- Website email address
- PO BOX address

Can we please have the files in a format that we can edit.

Reason: I need to consult my business partner with the designs so far and will make a decision from there.

Target Market(s)

Security Industry

Industry/Entity Type

Business

Contact Information for Business Card

- Mobile number
- Email address
- Website email address
- PO BOX address

Logo Text

HCSS and underneath the HCSS please add HARBOUR CREST SECURITY SERVICES PTY. LTD.

Font styles to use
Other font styles liked:
• bold type font

Colors
0255a3
000000

Requirements
Must have
• We are an Crest security company that provides a top quality manpower services to protect high rise buildings, retail and all type of properties and would like a new business card/logo look.
• - We would like the spot UV design.
• - Matt black (double sided).
• - We would like to incorporate a royal blue colour (feel free to experiment with it).
• - Feel free to try different lengths with the card to make it stand out more than a normal business card.
• - We would like the logo to be an eagle eye in the background (shines when card is tilted slightly in the background, either on the front, back or both sides of the card). Image attached as an example of eye shape (colour to be either black or royal blue).
• - HARBOUR CREST SECURITY SERVICES PTY. LTD. and HCSS to be placed on one side of the card and on the other side of the card to have;
• - Name in slightly bigger font than the position (directly on the bottom on the name).
• - Mobile number
• - Email address
• - Website email address
• - PO BOX address
• Can we please have the files in a format that we can edit.
Nice to have
• Feel free to try different lengths with the card to make it stand out more than a normal business card.
• Please find "URBAN JUNGLE" font attached and incorporate HCSS into the same style with building's inside the HCSS bold front also add HARBOUR into the bottom part of the S and follow on E - Crest on the bottom S - SECURITY on the bottom S - SERVICES on the bottom of each letter.
• other than that, I'll be happy with a bold modern font for the HCSS and HARBOUR CREST SECURITY SERVICES in a bold and thinner font underneath.

```html
<!DOCTYPE html>
<html lang="en">
<head>
<meta charset="utf-8">
<title>Harbour Crest Security – Business Card</title>
<link rel="stylesheet" href="https://fonts.googleapis.com/css2?family=Exo+2:wght@400;700;800&family=Oswald:wght@400;600&family=Open+Sans:wght@400&family=Source+Code+Pro:wght@400&display=swap">
<style>
  :root {
    --royal: #2a3a99;
    --royal-deep: #1f2c86;
    --royal-light: #3344a8;
    --ink: #111118;
    --grey: #8a8a8a;
    --paper: #ffffff;
    --stage: #2b2b2e;
  }
  * { margin: 0; padding: 0; box-sizing: border-box; }
  html, body {
    width: 1200px; height: 1000px; overflow: hidden;
    background: var(--stage);
  }
  .canvas { position: relative; width: 1200px; height: 1000px; }

  .card {
    position: absolute; left: 285px; width: 630px; height: 360px;
    border-radius: 26px; overflow: hidden;
  }

  /* Front */
  .card--front {
    top: 70px;
    background: linear-gradient(135deg, var(--royal-deep), var(--royal-light));
  }
  .front-lockup {
    position: absolute; left: 0; right: 0; top: 128px;
    display: flex; flex-direction: column; align-items: center;
    color: var(--paper);
  }
  .front-lockup .mark-dot {
    width: 46px; height: 46px; border-radius: 50%;
    background: var(--paper); margin-bottom: 14px;
  }
  .front-lockup .brand-name {
    font-family: "Exo 2", sans-serif; font-weight: 800;
    font-size: 30px; letter-spacing: 0.5px; line-height: 1;
  }
  .front-lockup .brand-sub {
    font-family: "Exo 2", sans-serif; font-weight: 400;
    font-size: 11px; letter-spacing: 1px; margin-top: 6px;
    padding: 3px 0; border-top: 1px solid rgba(255,255,255,.8);
    border-bottom: 1px solid rgba(255,255,255,.8);
    width: 380px; text-align: center;
  }

  /* Back */
  .card--back { top: 470px; background: var(--paper); }

  .person { position: absolute; left: 48px; top: 96px; }
  .person .name {
    font-family: "Oswald", sans-serif; font-weight: 600;
    font-size: 32px; color: var(--royal); letter-spacing: .5px; line-height: 1;
  }
  .person .role {
    font-family: "Exo 2", sans-serif; font-size: 15px; color: var(--grey);
    letter-spacing: .5px; margin-top: 4px;
  }

  .back-logo {
    position: absolute; right: 44px; top: 52px;
    display: flex; align-items: center; gap: 8px;
  }
  .back-logo .mark-dot {
    width: 30px; height: 30px; border-radius: 50%; background: var(--royal);
  }
  .back-logo .brand-text { text-align: center; }
  .back-logo .brand-name {
    font-family: "Exo 2", sans-serif; font-weight: 800;
    font-size: 17px; color: var(--ink); line-height: 1;
  }
  .back-logo .brand-sub {
    font-family: "Exo 2", sans-serif; font-size: 7px; color: var(--ink);
    letter-spacing: .6px; border-top: 1px solid var(--royal);
    border-bottom: 1px solid var(--royal); margin-top: 3px; padding: 1px 0;
  }

  .band-top {
    position: absolute; right: 0; top: 128px; width: 236px; height: 14px;
    background: var(--royal);
  }

  .contacts {
    position: absolute; left: 48px; top: 218px; list-style: none;
    font-family: "Open Sans", sans-serif; font-size: 14px; color: #333;
  }
  .contacts li { display: flex; align-items: center; gap: 10px; height: 21px; }
  .contacts svg { width: 12px; height: 12px; fill: var(--royal); }
  .contacts .accent { color: var(--royal); }

  .band-bottom-left {
    position: absolute; left: 0; bottom: 0; width: 200px; height: 22px;
    background: var(--royal);
  }
  .band-bottom-dot {
    position: absolute; left: 212px; bottom: 20px; width: 20px; height: 20px;
    border-radius: 50%; background: var(--royal);
  }
  .band-address {
    position: absolute; left: 244px; right: 0; bottom: 22px; height: 26px;
    background: var(--royal); color: var(--paper);
    font-family: "Source Code Pro", monospace; font-size: 13px;
    display: flex; align-items: center; padding-left: 26px; letter-spacing: .5px;
  }
  .band-base {
    position: absolute; left: 244px; right: 0; bottom: 0; height: 10px;
    background: var(--royal);
  }
</style>
</head>
<body>
<main class="canvas">

  <section class="card card--front" aria-label="Business card front">
    <div class="front-lockup">
      <span class="mark-dot"></span>
      <span class="brand-name">HARBOUR CREST SECURITY</span>
      <span class="brand-sub">SERVICES PTY. LTD. and HCSS</span>
    </div>
  </section>

  <section class="card card--back" aria-label="Business card back">
    <div class="back-logo">
      <span class="mark-dot"></span>
      <div class="brand-text">
        <div class="brand-name">HARBOUR CREST SECURITY</div>
        <div class="brand-sub">SERVICES PTY. LTD. and HCSS</div>
      </div>
    </div>
    <div class="band-top"></div>

    <div class="person">
      <div class="name">DANIEL CARTER</div>
      <div class="role">CO-FOUNDER</div>
    </div>

    <ul class="contacts">
      <li>
        <svg viewBox="0 0 24 24"><path d="M6.6 10.8a15 15 0 0 0 6.6 6.6l2.2-2.2a1 1 0 0 1 1-.25 11.4 11.4 0 0 0 3.6.6 1 1 0 0 1 1 1V20a1 1 0 0 1-1 1A17 17 0 0 1 3 4a1 1 0 0 1 1-1h3.5a1 1 0 0 1 1 1c0 1.25.2 2.45.6 3.6a1 1 0 0 1-.25 1z"/></svg>
        <span>+61 400 555 018</span>
      </li>
      <li>
        <svg viewBox="0 0 24 24"><path d="M2 5h20v14H2z M2 5l10 8 10-8" fill="none" stroke="currentColor"/><path d="M2 5h20v2l-10 7L2 7z"/><path d="M2 9l10 7 10-7v10H2z"/></svg>
        <span>info@harbourcrestmail.com</span>
      </li>
      <li>
        <svg viewBox="0 0 24 24"><path d="M10 2a8 8 0 0 1 6.3 12.9l5.4 5.4-1.4 1.4-5.4-5.4A8 8 0 1 1 10 2zm0 2a6 6 0 1 0 0 12 6 6 0 0 0 0-12z"/></svg>
        <span>www.<span class="accent">harbourcrestsec</span>.com</span>
      </li>
    </ul>

    <div class="band-bottom-left"></div>
    <div class="band-bottom-dot"></div>
    <div class="band-address">PO Box 418, Harbourside 2000</div>
    <div class="band-base"></div>
  </section>

</main>
</body>
</html>
```